Life Coaching business needs a new flyer

We are an Australian business that specialises in Life Coaching, Career Coaching, Health and Wellness Coaching, Yoga and Pilates. We need a A4 double sided flyer that is full colour and folded to DL format. I have attached a couple of designs that I like and some pictures and would like the flyer to be bright yet stylish.

Industry/Entity Type

Life Coaching

```html
<!DOCTYPE html>
<html lang="en">
<head>
<meta charset="utf-8">
<title>Brightway Coaching – Trifold Brochure Front</title>
<link href="https://fonts.googleapis.com/css2?family=Raleway:wght@400;500;700&display=swap" rel="stylesheet">
<style>
:root{
  --page-bg:#eceae6;
  --paper:#ffffff;
  --blue:#1778c8;
  --heading-blue:#1a6fc0;
  --name-blue:#1f7ac7;
  --green:#5cb646;
  --ink:#1c1c1c;
  --quote-grey:#b9b9b9;
  --label:#ffffff;
}
*{box-sizing:border-box;margin:0;padding:0}
html,body{width:1200px;height:1000px;overflow:hidden}
body{background:var(--page-bg);font-family:'Raleway',sans-serif;color:var(--ink);position:relative}
.brochure{position:absolute;left:69px;top:44px;width:1061px;height:820px;background:var(--paper);display:flex;box-shadow:0 2px 10px rgba(0,0,0,.25)}
.panel{position:relative;height:100%}
.panel--testimonials{width:351px}
.panel--intro{width:353px}
.panel--services{width:357px}

/* testimonials */
.testimonials{padding:30px 22px 0 29px}
.testimonials__title{color:var(--heading-blue);font-weight:700;font-size:16px;margin-bottom:8px}
.testimonial{font-size:12px;line-height:14.9px;margin-bottom:14px;position:relative}
.testimonial__quote{color:var(--quote-grey);font-weight:700;font-size:18px;line-height:0;position:relative;top:4px}
.testimonial__author{color:var(--heading-blue);display:block}
.photo{display:block}
.photo--group{position:absolute;left:0;bottom:0;width:351px;height:242px;background:linear-gradient(160deg,#f7e1a8 0%,#e6a85e 45%,#8a6a52 80%,#5b5a63 100%)}

/* intro */
.intro{background:var(--blue);height:528px;color:#fff;text-align:center;padding-top:32px}
.offer{margin:0 auto;width:304px;height:84px;border:1px dashed rgba(255,255,255,.8);border-radius:8px;padding-top:9px}
.offer__line{font-size:18.5px;line-height:22px}
.offer__note{font-size:14px;line-height:18px}
.photo--founders{margin:35px auto 0;width:263px;height:173px;border:3px solid #fff;border-radius:10px;background:linear-gradient(135deg,#6e5d52 0%,#8b8078 50%,#a9aeb6 100%)}
.intro__text{font-size:14px;line-height:19.3px;margin:20px auto 0;width:276px}
.intro__text + .intro__text{margin-top:19px}
.brand{display:flex;align-items:center;justify-content:center;gap:10px;color:var(--name-blue);font-weight:500;text-align:center}
.brand__dot{width:28px;height:28px;border-radius:50%;background:var(--green);flex:none}
.brand__name{font-size:22px;line-height:26px}
.brand--intro{height:195px}
.contact{position:absolute;left:0;bottom:0;width:100%;height:97px;background:var(--green);color:#fff;text-align:center;padding-top:9px}
.contact__phone{font-size:23px;line-height:28px;display:flex;align-items:center;justify-content:center;gap:6px}
.contact__line{font-size:13px;line-height:21px;display:flex;align-items:center;justify-content:center;gap:6px}

/* services */
.brand--services{height:161px}
.service{position:relative}
.service__label{position:absolute;left:10px;top:8px;color:var(--label);font-weight:700;font-size:11px;letter-spacing:.2px}
.service--life{height:268px;background:linear-gradient(180deg,#2f7fd3 0%,#5da3e6 60%,#d9eaf7 100%)}
.service--meditation{height:157px;margin-top:5px;background:linear-gradient(180deg,#5a9fd8 0%,#9cc7ea 45%,#7b9a5a 80%,#8f9f77 100%)}
.service--yoga{height:224px;margin-top:5px;background:linear-gradient(180deg,#bfd6ea 0%,#d8e6ef 55%,#e9e7e2 100%)}
</style>
</head>
<body>
<main class="brochure">
  <section class="panel panel--testimonials">
    <div class="testimonials">
      <h2 class="testimonials__title">Happy Clients Testimonials</h2>
      <p class="testimonial"><span class="testimonial__quote">“</span>I have lost 10 kilos and now have the energy to play with my kids. Thanks Mara for you support/guidance and helping me get rid of my limiting beliefs. I feel I can achieve anything now! The sky's the limit <span class="testimonial__quote">”</span><span class="testimonial__author">EMMA, Mosman</span></p>
      <p class="testimonial"><span class="testimonial__quote">“</span>I had always wanted to start up own café however every time it came to putting it into practice I would procrastinate and not achieve anything. I became overwhelmed with the whole process and never achieved anything. Mara put it into bite sized chunks and helped me to set small achievable goals. I am now a happy café owner.<span class="testimonial__quote">”</span><span class="testimonial__author">CLAIRE, Double Bay</span></p>
      <p class="testimonial"><span class="testimonial__quote">“</span>Mara has helped to change my life around in all aspects. I would have been lost without her. Thanks Mara for your professionalism, support and guidance.<span class="testimonial__quote">”</span><span class="testimonial__author">TESSA, Cremorne</span></p>
      <p class="testimonial"><span class="testimonial__quote">“</span>I was so busy with kids, work, and my husband I lost who I was. Mara has helped me find the person I am again.<span class="testimonial__quote">”</span><span class="testimonial__author">HANNAH, Chatswood</span></p>
      <p class="testimonial"><span class="testimonial__quote">“</span>When I started with Coach Mara, I didn't know anything about coaching. I called her because she helped a friend of mine make a career change that was a perfect fit for her. I had the opportunity to make a change too and did not know where to start. I am now in a job that I love. I would recommend Mara to everyone.<span class="testimonial__quote">”</span><span class="testimonial__author">DANIEL, Texas America</span></p>
    </div>
    <div class="photo photo--group" role="img" aria-label="Photo of a group of happy friends celebrating by a coastal road at sunset"></div>
  </section>

  <section class="panel panel--intro">
    <div class="intro">
      <div class="offer">
        <p class="offer__line">Free Introductory Life Coaching</p>
        <p class="offer__line">Phone/Video session - 20 mins</p>
        <p class="offer__note">(To see if coaching is right for you)</p>
      </div>
      <div class="photo photo--founders" role="img" aria-label="Portrait photo of the two coaches"></div>
      <p class="intro__text">Brightway Coaching and Meditation Studio is a professional service that can help you achieve the goals that you are looking for in Life Coaching, Meditation, and Yoga/Pilates.</p>
      <p class="intro__text">If you are ready to take your life to the next level and would like to know more, please contact us.</p>
    </div>
    <div class="brand brand--intro">
      <span class="brand__dot"></span>
      <span class="brand__name">Brightway Coaching</span>
    </div>
    <div class="contact">
      <p class="contact__phone">
        <svg width="18" height="18" viewBox="0 0 24 24" fill="none" stroke="#fff" stroke-width="2"><circle cx="12" cy="12" r="10"/><path d="M9 7l2 3-1.5 1.5a7 7 0 0 0 3 3L14 13l3 2-1 2c-4 0-9-5-9-9z" fill="#fff" stroke="none"/></svg>
        02 9000 4127
      </p>
      <p class="contact__line">
        <svg width="14" height="11" viewBox="0 0 14 11" fill="none" stroke="#fff" stroke-width="1.2"><rect x=".6" y=".6" width="12.8" height="9.8"/><path d="M.6 .6L7 6l6.4-5.4"/></svg>
        hello@brightwaycoaching.com.au
      </p>
      <p class="contact__line">www.brightwaycoaching.com.au</p>
    </div>
  </section>

  <section class="panel panel--services">
    <div class="brand brand--services">
      <span class="brand__dot"></span>
      <span class="brand__name">Brightway Coaching</span>
    </div>
    <div class="service service--life" role="img" aria-label="Photo of a signpost pointing to life, balance, family, career, health and friends under a blue sky">
      <span class="service__label">LIFE COACHING</span>
    </div>
    <div class="service service--meditation" role="img" aria-label="Photo of a group meditating on mats by the water">
      <span class="service__label">MEDITATION</span>
    </div>
    <div class="service service--yoga" role="img" aria-label="Photo of two people in a yoga tree pose on a beach">
      <span class="service__label">YOGA/PILATES</span>
    </div>
  </section>
</main>
</body>
</html>
```